Oil and Gas Exploration and Production company needs a business card design

We need a business card design using our logo and colors in the logo. We want a mainstream design.

```html
<!DOCTYPE html>
<html lang="en">
<head>
<meta charset="utf-8">
<title>Sol Basin Oil &amp; Gas – Business Card</title>
<link rel="stylesheet" href="https://fonts.googleapis.com/css2?family=Fira+Sans:wght@400;500;700&display=swap">
<style>
  :root {
    --page-bg: #e9e6e1;
    --card-bg: #f8f5ef;
    --gold: #c9a033;
    --ink: #1d1b18;
    --rule: #d8bd73;
  }
  * { box-sizing: border-box; margin: 0; padding: 0; }
  html, body {
    width: 1200px; height: 1200px; overflow: hidden;
    background: var(--page-bg);
    font-family: "Fira Sans", Arial, sans-serif;
  }
  .card {
    position: absolute; left: 100px; top: 314px;
    width: 1000px; height: 572px;
    background: var(--card-bg);
    box-shadow: 0 10px 30px rgba(0,0,0,.12);
    overflow: hidden;
  }
  .brand {
    position: absolute; left: 64px; top: 92px;
    display: flex; align-items: center; gap: 16px;
  }
  .brand-dot { width: 38px; height: 38px; border-radius: 50%; background: var(--gold); }
  .brand-name {
    font-weight: 700; font-size: 52px; line-height: 1; color: var(--ink);
    letter-spacing: -0.5px;
  }
  .person { position: absolute; left: 64px; top: 290px; }
  .person-name { font-size: 46px; font-weight: 400; color: var(--gold); line-height: 1.05; }
  .person-role { font-size: 28px; color: var(--ink); margin-top: 4px; }
  .person-rule {
    position: absolute; left: 64px; top: 384px;
    width: 560px; height: 2px; background: var(--rule);
  }
  .contacts {
    position: absolute; left: 64px; top: 400px;
    list-style: none; font-size: 27px; color: var(--ink);
  }
  .contacts li { display: flex; align-items: center; gap: 12px; height: 40px; }
  .contacts svg { width: 26px; height: 26px; fill: var(--ink); flex: none; }
  .divider {
    position: absolute; left: 470px; top: 404px;
    width: 2px; height: 92px; background: var(--ink); opacity: .7;
  }
  .address {
    position: absolute; left: 498px; top: 404px;
    font-size: 27px; color: var(--ink); line-height: 40px;
  }
  .address-line { display: flex; align-items: center; gap: 12px; }
  .address-line svg { width: 22px; height: 28px; fill: var(--ink); }
  .address-line.indent { padding-left: 34px; }
  .band-thin {
    position: absolute; left: 0; right: 0; bottom: 50px;
    height: 4px; background: var(--gold);
  }
  .band-thick {
    position: absolute; left: 0; right: 0; bottom: 0;
    height: 34px; background: var(--gold);
  }
</style>
</head>
<body>
  <div class="card">
    <div class="brand">
      <span class="brand-dot"></span>
      <span class="brand-name">Sol Basin Oil &amp; Gas</span>
    </div>

    <div class="person">
      <p class="person-name">JOHN DOE</p>
      <p class="person-role">Director</p>
    </div>
    <div class="person-rule"></div>

    <ul class="contacts">
      <li>
        <svg viewBox="0 0 24 24" aria-hidden="true"><path d="M3 8c0-2 4-4 9-4s9 2 9 4v2h-5V8H8v2H3zm4 3h10l3 9H4z"/></svg>
        1-234-567890
      </li>
      <li>
        <svg viewBox="0 0 24 24" aria-hidden="true"><path d="M2 5h20v14H2zm2 2v.5l8 5.5 8-5.5V7zm0 3v7h16v-7l-8 5.5z"/></svg>
        john@solbasin.com
      </li>
      <li>
        <svg viewBox="0 0 24 24" aria-hidden="true"><path d="M12 2a10 10 0 1 0 0 20 10 10 0 0 0 0-20zm0 2c1.3 1.5 2.2 3.6 2.4 7H9.6c.2-3.4 1.1-5.5 2.4-7zM4.1 11a8 8 0 0 1 4-6c-.9 1.7-1.4 3.7-1.5 6zm0 2h3.5c.1 2.3.6 4.3 1.5 6a8 8 0 0 1-5-6zm5.5 0h4.8c-.2 3.4-1.1 5.5-2.4 7-1.3-1.5-2.2-3.6-2.4-7zm6.8 0h3.5a8 8 0 0 1-5 6c.9-1.7 1.4-3.7 1.5-6zm0-2c-.1-2.3-.6-4.3-1.5-6a8 8 0 0 1 5 6z"/></svg>
        www.solbasin.com
      </li>
    </ul>

    <div class="divider"></div>

    <div class="address">
      <p class="address-line">
        <svg viewBox="0 0 20 26" aria-hidden="true"><path d="M10 0a9 9 0 0 0-9 9c0 7 9 17 9 17s9-10 9-17a9 9 0 0 0-9-9zm0 5a4 4 0 1 1 0 8 4 4 0 0 1 0-8z"/></svg>
        Dummy city
      </p>
      <p class="address-line indent">Dummy Country Land</p>
    </div>

    <div class="band-thin"></div>
    <div class="band-thick"></div>
  </div>
</body>
</html>
```